Business card for Sports Apparel business

DOUBLE SIDED DESIGN
We need business cards for a new sports apparel business. We are developing a protective headband for soccer initially.
Torvalle is focused on designing and developing head protection products to reduce the likelihood of concussion when playing sports. Exploring and understanding medical insights, material science research, current and former players experiences and governing bodies guidelines has allowed Torvalle to develop the safety, style, form and function requirements of a suitable product to bring to market.
Target Market(s)
Mums buying kits for the sons and daughters. Amateur footballers.
Industry/Entity Type
Sporting Good
Contact Information for Business Card
Martin Ashworth - CEO
Mobile: +44 7431589027
Email: martin@torvalle.co.uk
Tel: 0208 5519372
Helena Pargeter - COO
Mob: +44 7385 640117
Email: helena@torvalle.co.uk
Tel: 0208 5519372
Duncan Farrow - CCO
Mob: +44 7564 293081
Email: duncan@torvalle.co.uk
Tel: 0208 5519372
Look and feel
Each slider illustrates characteristics of the customer's brand and the style your logo design should communicate.

```html
<!DOCTYPE html>
<html lang="en">
<head>
<meta charset="utf-8">
<title>Torvalle Business Card</title>
<link href="https://fonts.googleapis.com/css2?family=Montserrat:wght@400;600&display=swap" rel="stylesheet">
<style>
  :root {
    --backdrop: #e4e4e4;
    --card-dark: #111111;
    --card-light: #ffffff;
    --brand-blue: #1d65a6;
    --text-grey: #555a60;
    --text-white: #ffffff;
  }
  * { margin: 0; padding: 0; box-sizing: border-box; }
  html, body { width: 1200px; height: 896px; overflow: hidden; }
  body {
    background: var(--backdrop);
    font-family: "Montserrat", sans-serif;
    display: flex;
    align-items: center;
    justify-content: center;
    gap: 48px;
  }
  .card {
    width: 525px;
    height: 300px;
    border-radius: 22px;
    box-shadow: 0 10px 28px rgba(0,0,0,0.22);
    position: relative;
    overflow: hidden;
  }
  .card-front {
    background: var(--card-dark);
    display: flex;
    align-items: center;
    justify-content: center;
  }
  .brand-name {
    font-weight: 600;
    letter-spacing: 0.08em;
    text-transform: uppercase;
  }
  .card-front .brand-name {
    color: var(--text-white);
    font-size: 50px;
  }
  .card-back {
    background: var(--card-light);
    display: flex;
    align-items: center;
    padding: 0 36px 0 40px;
  }
  .card-back .brand-name {
    color: var(--brand-blue);
    font-size: 32px;
    width: 222px;
  }
  .divider {
    display: flex;
    flex-direction: column;
    justify-content: space-between;
    height: 130px;
    margin: 0 22px 0 6px;
  }
  .divider span {
    display: block;
    width: 2px;
    height: 40px;
    background: var(--brand-blue);
  }
  .divider span:last-child { height: 52px; }
  .details { display: flex; flex-direction: column; height: 130px; justify-content: space-between; }
  .person-name {
    color: var(--brand-blue);
    font-weight: 600;
    font-size: 17px;
    letter-spacing: 0.08em;
    text-transform: uppercase;
  }
  .person-role {
    color: var(--text-grey);
    font-size: 12px;
    letter-spacing: 0.08em;
    margin-top: 4px;
  }
  .contact-list { list-style: none; }
  .contact-list li {
    display: flex;
    align-items: center;
    gap: 8px;
    color: var(--text-grey);
    font-size: 12px;
    line-height: 1.6;
  }
  .contact-list svg { width: 10px; height: 10px; fill: none; stroke: var(--brand-blue); stroke-width: 1.6; }
  .contact-list .accent { color: var(--brand-blue); }
</style>
</head>
<body>
  <section class="card card-front" aria-label="Card front">
    <span class="brand-name">Torvalle</span>
  </section>

  <section class="card card-back" aria-label="Card back">
    <span class="brand-name">Torvalle</span>
    <div class="divider"><span></span><span></span></div>
    <div class="details">
      <div>
        <p class="person-name">Helena Pargeter</p>
        <p class="person-role">COO</p>
      </div>
      <ul class="contact-list">
        <li><svg viewBox="0 0 10 10"><path d="M2 1 L4 3 L3 4 Q4 6 6 7 L7 6 L9 8 L8 9 Q3 8 1 2 Z"/></svg>0208 5519372</li>
        <li><svg viewBox="0 0 10 10"><rect x="2" y="1" width="6" height="8" rx="1"/></svg>+44 7385 640117</li>
        <li><svg viewBox="0 0 10 10"><rect x="1" y="2" width="8" height="6"/><path d="M1 2 L5 5.5 L9 2"/></svg>helena@torvalle.co.uk</li>
        <li><svg viewBox="0 0 10 10"><circle cx="5" cy="5" r="4"/><path d="M1 5 H9 M5 1 Q2.5 5 5 9 M5 1 Q7.5 5 5 9"/></svg>www.<span class="accent">torvalle</span>.co.uk</li>
      </ul>
    </div>
  </section>
</body>
</html>
```